Heron Loan Partners Business Card

We need a business card design for our mortgage servicing company. In addition to servicing the loans of homeowners, we help homeowners with purchasing their homes and any mortgage refinancing. We would like to see designs that use the colors in the logo attached below (gold-ish yellow and navy blue), and any other design you deem fit! The design should communicate a simpler life with smart mortgages provided by Heron.

```html
<!DOCTYPE html>
<html lang="en">
<head>
<meta charset="utf-8">
<title>Heron Loan Partners — Business Card</title>
<link rel="stylesheet" href="https://fonts.googleapis.com/css2?family=Crimson+Pro:wght@400;600&display=swap">
<style>
  :root {
    --bg: #e7e7e5;
    --card: #ffffff;
    --gold: #c9a03a;
    --navy: #23204f;
    --ink: #3a3a3a;
    --rule: #8c8aa3;
  }
  * { margin: 0; padding: 0; box-sizing: border-box; }
  html, body { width: 1200px; height: 900px; overflow: hidden; }
  body {
    background: var(--bg);
    font-family: "Crimson Pro", Georgia, serif;
    color: var(--ink);
    position: relative;
  }
  .card {
    position: absolute;
    left: 320px;
    width: 560px;
    height: 320px;
    background: var(--card);
    box-shadow: 0 6px 18px rgba(0,0,0,.18);
  }
  .card--back { top: 90px; }
  .card--front { top: 470px; }

  .brand {
    position: absolute;
    font-family: "Crimson Pro", Georgia, serif;
    font-weight: 600;
    color: var(--gold);
    white-space: nowrap;
  }
  .brand__dot {
    display: inline-block;
    width: 12px; height: 12px;
    border-radius: 50%;
    background: var(--gold);
    margin-right: 12px;
    vertical-align: middle;
  }

  .card--back .website {
    position: absolute;
    top: 30px; right: 34px;
    font-size: 15px;
    letter-spacing: 4px;
    color: var(--ink);
  }
  .website__name { color: var(--gold); }
  .card--back .brand { left: 110px; top: 200px; font-size: 40px; }

  .card--front .brand { left: 0; right: 0; top: 40px; text-align: center; font-size: 40px; }
  .rule { position: absolute; height: 1px; background: var(--rule); }
  .rule--top { left: 150px; width: 370px; top: 165px; }
  .rule--mid { left: 50px; width: 230px; top: 218px; }

  .person { position: absolute; left: 50px; top: 184px; font-size: 20px; }
  .person__name { color: var(--gold); letter-spacing: .5px; }
  .person__sep { color: var(--gold); margin: 0 6px; }
  .person__role { color: var(--ink); }

  .contacts { position: absolute; left: 50px; top: 228px; list-style: none; font-size: 16px; line-height: 25px; }
  .contacts li { display: flex; align-items: center; gap: 10px; }
  .contacts svg { width: 15px; height: 15px; fill: none; stroke: var(--gold); stroke-width: 1.6; }

  .divider { position: absolute; left: 330px; top: 232px; width: 1px; height: 62px; background: var(--gold); }
  .address { position: absolute; left: 348px; top: 234px; font-size: 18px; line-height: 26px; font-style: normal; }
</style>
</head>
<body>
  <section class="card card--back">
    <p class="website">www.<span class="website__name">heronloan</span>.com</p>
    <div class="brand"><span class="brand__dot"></span>Heron Loan Partners</div>
  </section>

  <section class="card card--front">
    <div class="brand"><span class="brand__dot"></span>Heron Loan Partners</div>
    <div class="rule rule--top"></div>
    <p class="person"><span class="person__name">JOHN SMITH</span><span class="person__sep">|</span><span class="person__role">Director</span></p>
    <div class="rule rule--mid"></div>
    <ul class="contacts">
      <li><svg viewBox="0 0 16 16"><path d="M3 2l3 1 1 3-2 1a8 8 0 0 0 4 4l1-2 3 1 1 3-2 1C7 14 2 9 2 4z"/></svg>300-200-9000</li>
      <li><svg viewBox="0 0 16 16"><rect x="1.5" y="3.5" width="13" height="9"/><path d="M1.5 3.5l6.5 5 6.5-5"/></svg>info@heronloan.com</li>
      <li><svg viewBox="0 0 16 16"><circle cx="8" cy="8" r="6.5"/><ellipse cx="8" cy="8" rx="3" ry="6.5"/><path d="M1.5 8h13"/></svg>www.heronloan.com</li>
    </ul>
    <div class="divider"></div>
    <address class="address">00 dummy city<br>place 0000</address>
  </section>
</body>
</html>
```